White Paper and One-Page Advertisement for TELVORISH-QM

I need both documents to be better formatted and designed so they look professional, not something someone with mediocre word skills put together. They will go out to 1000s of industry professionals, and they need to look sharp. I need them to have my company's color palate logo, and branding on it similar to how it is now, but better. Please do not change any of the written content, but it can be arranged in any other format you think is better. Smart art and things i've already used can be omitted in favor of better designs. The developer is free to use their creativity. White paper should not be longer than the three pages unless necessary.

Target Market(s)

Life Sciences supply chain professionals

Colors
33b8a4
0592cd
9bcb3c
fbee3e
3277b5

Requirements
Must have
• Must be professional looking and not look like something done in word. Please use the color palate as seen on the documents.
Should not have
• Any changes to the written content.

```html
<!DOCTYPE html>
<html lang="en">
<head>
<meta charset="utf-8">
<title>Changing Pharma's Paradigm of Waste – TELVORISH-QM</title>
<link rel="stylesheet" href="https://fonts.googleapis.com/css2?family=Barlow:ital,wght@0,400;0,600;0,700;1,400&family=Barlow+Condensed:wght@600&display=swap">
<style>
  :root {
    --page-bg: #dde8c5;
    --sheet: #ffffff;
    --ink: #1a1a1a;
    --lime: #8dc03f;
    --lime-band: #c7dc99;
    --forest: #2f6b55;
    --teal-dark: #4d7f6e;
    --teal-mid: #78a588;
    --sage: #9bbd84;
    --overview: #3e4a44;
  }
  * { margin: 0; padding: 0; box-sizing: border-box; }
  html, body { width: 842px; height: 1200px; overflow: hidden; }
  body {
    background: var(--page-bg);
    font-family: "Barlow", sans-serif;
    color: var(--ink);
    position: relative;
  }
  .page-number {
    position: absolute; left: 67px; top: 35px;
    font-weight: 700; font-size: 13px; letter-spacing: .2px;
  }
  .sheet {
    position: absolute; left: 42px; top: 77px;
    width: 758px; height: 711px;
    background: var(--sheet);
  }
  .brand {
    position: absolute; left: 64px; top: 82px;
    display: flex; align-items: center; gap: 10px;
  }
  .brand-dot {
    width: 40px; height: 40px; border-radius: 50%;
    background: var(--forest);
  }
  .brand-name {
    font-weight: 700; font-size: 26px; color: var(--forest);
    letter-spacing: .5px;
  }
  .title {
    position: absolute; left: 58px; top: 262px;
    font-weight: 700; font-size: 47px; line-height: 48px;
    letter-spacing: .3px; text-transform: uppercase;
  }
  .subtitle {
    position: absolute; left: 58px; top: 369px;
    font-weight: 700; font-size: 24.5px; line-height: 32px;
    color: var(--lime);
  }
  .section-rule {
    position: absolute; left: 58px; top: 524px;
    width: 544px; height: 2px; background: var(--lime);
  }
  .section-label {
    position: absolute; right: 58px; top: 501px;
    font-family: "Barlow Condensed", sans-serif; font-weight: 600;
    font-size: 28px; color: var(--overview); letter-spacing: .3px;
  }
  .overview {
    position: absolute; left: 58px; top: 538px; width: 642px;
    font-size: 10.6px; line-height: 15.2px;
  }
  .overview p + p { margin-top: 15px; }
  .accent-band {
    position: absolute; left: 42px; top: 788px;
    width: 758px; height: 18px; background: var(--lime-band);
  }
  .photo {
    position: absolute; top: 806px; height: 206px;
  }
  .photo-infant { left: 42px; width: 268px; background: linear-gradient(135deg, #cbb9a7, #9c8472); }
  .photo-elder { left: 310px; width: 256px; background: linear-gradient(135deg, #a98a55, #d9cfc0 55%, #7a6e86); }
  .photo-woman { left: 566px; width: 234px; background: linear-gradient(135deg, #5a6a4a, #a77a5e 55%, #c9b8a0); }
  .footer-panel {
    position: absolute; left: 42px; top: 1012px;
    width: 758px; height: 136px;
    background: linear-gradient(180deg, var(--teal-mid), var(--teal-dark));
  }
  .caption {
    position: absolute; left: 42px; top: 982px;
    width: 619px; height: 64px;
    background: linear-gradient(90deg, var(--teal-dark), var(--sage) 70%, #a9c78f);
    border-bottom-right-radius: 10px;
    padding: 8px 0 0 58px;
    color: #fff; font-style: italic; font-size: 18.5px; line-height: 24px;
  }
  .author {
    position: absolute; right: 100px; top: 1061px;
    text-align: right; color: #fff; font-weight: 700;
    font-size: 14px; line-height: 18.5px;
  }
</style>
</head>
<body>
  <div class="page-number">PAGE 1</div>

  <main class="sheet">
    <div class="brand">
      <span class="brand-dot"></span>
      <span class="brand-name">TELVORISH-QM</span>
    </div>

    <h1 class="title">Changing Pharma’s<br>Paradigm of Waste</h1>
    <h2 class="subtitle">How Pharma’s Demand Volatility Could Be<br>Costing You Millions in Material Write-downs<br>&amp; Procurement</h2>

    <div class="section-rule"></div>
    <div class="section-label">OVERVIEW</div>

    <section class="overview">
      <p>Demand volatility is a challenge for very supply chain.&nbsp; It strikes at the end of supply chains causing a "bullwhip effect" that becomes exponentially more impactful further back in the chain.&nbsp; For Pharma, the effect is strongest in manufacturing and procurement, specifically with starting raw materials and consumables.</p>
      <p>Swings in demand can cripple launches, cause stock-outs, inflate material prices, make lean planning ineffective, and cause significant write-downs of residual/obsolete materials; ultimately inflating CoGS and reducing net income.&nbsp; These swings can also cause inventory costs to inflate, materials to expire or become obsolete, higher disposal fees, and a larger carbon footprint. The yearly financial impacts are staggering considering Pharma’s economic footprint. Twenty of Pharma’s top 100 companies were sampled using 2015 &amp; 2016 financial figures1-2-3-4.&nbsp; Industry estimates for waste include:</p>
    </section>
  </main>

  <div class="accent-band"></div>
  <div class="photo photo-infant" role="img" aria-label="Photo of a smiling baby in a knitted hood"></div>
  <div class="photo photo-elder" role="img" aria-label="Photo of a smiling elderly woman with glasses"></div>
  <div class="photo photo-woman" role="img" aria-label="Photo of a young woman with earrings in profile"></div>

  <div class="footer-panel"></div>
  <div class="caption">Every new journey of change and innovation we take is for them...<br>The Patient</div>
  <div class="author">Dana Holloway<br>August 2018</div>
</body>
</html>
```